Detail Shop Business card design

i need a business card design for my new detailing company called 'Brisk's Polish Works'. i want an all black and white design . simple, direct and to the point. i want the designer to choose a fitting font to match the logothe front should have logo, address, phone and email and the back side should have a slogan and text indicating that we offer services on anything including cars, trucks, motorcycles and RVs. slogan will read "we take pride in your ride"
maybe also very small on the back side the IG icon with Brisks_Polish_Works

phone 208.417.6352
address 3847 E Larkin Ave
Spokane WA 99214
email: BrisksPolish@mailvexo.com

Target Market(s)

all ages , auto enthusiasts

Industry/Entity Type

Automotive

Contact Information for Business Card

the front should have logo, address, phone and email and the back side should have a slogan and text indicating that we offer services on anything including cars, trucks, motorcycles and RVs. slogan will read "we take pride in your ride"

phone 208.417.6352
address 3847 E Larkin Ave
Spokane WA 99214

Colors
000000
ffffff

Requirements
Must have
• bold font and very simple design with good spacing
Nice to have
• anything creative from the designer indicating we service any types of vehicles
Should not have
• any colors ,

```html
<!DOCTYPE html>
<html lang="en">
<head>
<meta charset="utf-8">
<title>Brisk's Polish Works – Business Card</title>
<link href="https://fonts.googleapis.com/css2?family=Lato:wght@400;700&family=Yellowtail&display=swap" rel="stylesheet">
<style>
  :root {
    --ink: #000000;
    --paper: #ffffff;
    --paper-soft: #f6f6f6;
    --stage: #3a3a3a;
  }
  * { margin: 0; padding: 0; box-sizing: border-box; }
  html, body { width: 1200px; height: 802px; overflow: hidden; background: var(--stage); }
  .stage { position: relative; width: 1200px; height: 802px; }
  .card {
    position: absolute; top: 274px; width: 442px; height: 264px; overflow: hidden;
    font-family: 'Lato', sans-serif;
  }
  .card-front { left: 136px; }
  .card-back { left: 624px; }
  .card-shape { position: absolute; inset: 0; width: 100%; height: 100%; }
  .brand {
    position: absolute; width: 170px; text-align: center;
    font-family: 'Lato', sans-serif; font-weight: 700; font-size: 19px; line-height: 1.2;
    color: var(--ink); display: flex; flex-direction: column; align-items: center; gap: 8px;
  }
  .brand-dot { width: 14px; height: 14px; border-radius: 50%; background: var(--ink); }
  .card-front .brand { left: 23px; top: 62px; }
  .card-back .brand { left: 239px; top: 62px; }
  .contact {
    position: absolute; right: 28px; top: 122px; text-align: right;
    color: var(--paper); font-size: 12.2px; line-height: 16px;
  }
  .contact-line { display: flex; justify-content: flex-end; align-items: center; gap: 4px; }
  .contact-gap { margin-top: 8px; }
  .contact-gap-lg { margin-top: 15px; }
  .icon { width: 11px; height: 11px; flex: none; }
  .social-dot { width: 15px; height: 15px; border-radius: 50%; background: var(--paper); flex: none; margin-left: 2px; }
  .services {
    position: absolute; left: 20px; top: 100px; width: 155px;
    font-family: 'Yellowtail', cursive; font-size: 16.5px; line-height: 24.5px;
    color: var(--paper); letter-spacing: 0.2px;
  }
  .services-line { display: block; white-space: nowrap; }
  .slogan {
    position: absolute; left: 20px; top: 213px;
    font-size: 13.5px; font-weight: 400; letter-spacing: 0.1px;
    color: var(--paper); text-transform: uppercase; white-space: nowrap;
  }
</style>
</head>
<body>
<main class="stage">

  <section class="card card-front" aria-label="Card front">
    <svg class="card-shape" viewBox="0 0 545 325" preserveAspectRatio="none" aria-hidden="true">
      <rect width="545" height="325" fill="var(--paper-soft)"/>
      <path d="M288,0 C338,70 325,228 183,325 L545,325 L545,0 Z" fill="var(--ink)"/>
      <path d="M299,0 C349,72 336,232 196,325" fill="none" stroke="var(--paper)" stroke-width="3"/>
    </svg>
    <div class="brand"><span class="brand-dot"></span><span>Brisk's Polish Works</span></div>
    <div class="contact">
      <div class="contact-line">3847 E Larkin Ave</div>
      <div class="contact-line">Spokane WA 99214</div>
      <div class="contact-line contact-gap">208.417.6352
        <svg class="icon" viewBox="0 0 12 12" aria-hidden="true"><path d="M1,4 Q6,0 11,4 L9,5 L8,3.5 L4,3.5 L3,5 Z M3,6 L9,6 L10,10 L2,10 Z" fill="var(--paper)"/></svg>
      </div>
      <div class="contact-line">BrisksPolish@mailvexo.com
        <svg class="icon" viewBox="0 0 12 12" aria-hidden="true"><rect x="1" y="3" width="10" height="7" fill="var(--paper)"/><path d="M1,3 L6,7 L11,3" fill="none" stroke="var(--ink)" stroke-width="1"/></svg>
      </div>
      <div class="contact-line contact-gap-lg">Brisks_Polish_Works<span class="social-dot"></span></div>
    </div>
  </section>

  <section class="card card-back" aria-label="Card back">
    <svg class="card-shape" viewBox="0 0 545 325" preserveAspectRatio="none" aria-hidden="true">
      <rect width="545" height="325" fill="var(--paper)"/>
      <path d="M264,0 C216,70 226,232 359,325 L0,325 L0,0 Z" fill="var(--ink)"/>
      <path d="M253,0 C205,72 214,236 345,325" fill="none" stroke="var(--paper)" stroke-width="3"/>
    </svg>
    <p class="services">
      <span class="services-line">We offer services on</span>
      <span class="services-line">anything including</span>
      <span class="services-line">cars, trucks</span>
      <span class="services-line">motorcycles and RVs.</span>
    </p>
    <p class="slogan">We take pride in your ride</p>
    <div class="brand"><span class="brand-dot"></span><span>Brisk's Polish Works</span></div>
  </section>

</main>
</body>
</html>
```